Marcus Delbridge Finance

Need a personal website advertising Equipment Finance,Business Finance,Commercial Finance, Construction Finance, Bridging Finance. Similar websites are www.corvalend.com.au / www.tarmivest.com.au / www.qbr7.com.au /wwwhalvecredit.com.au

Target Market(s)

Business People

Industry/Entity Type

Business

Number of Pages Required

3 page

Font styles to use
Serif
Sans Serif

Requirements
Must have
• All i want is a simple corporate looking website advertising Equipment Finance, Commercial Finance, Construction Finance, Business Finance, Bridging Finance,

```html
<!DOCTYPE html>
<html lang="en">
<head>
<meta charset="utf-8">
<title>Marcus Delbridge Finance</title>
<link rel="stylesheet" href="https://fonts.googleapis.com/css2?family=Open+Sans:wght@400;600;700&family=Raleway:wght@400;500;600;700&display=swap">
<style>
  :root {
    --green: #a2bd1e;
    --blue: #1b8bbf;
    --band: #1a8ab8;
    --ink: #222;
    --text: #5a5a5a;
    --grey-bg: #f1f1f1;
    --white: #fff;
    --footer: #2c2c2c;
    --footer-line: #444;
    --footer-ring: #9a9a9a;
  }
  * { box-sizing: border-box; margin: 0; padding: 0; }
  html, body { width: 1200px; height: 3766px; overflow: hidden; }
  body { position: relative; font-family: "Open Sans", Arial, sans-serif; color: var(--text); background: var(--white); }

  .btn {
    display: inline-flex; align-items: center; gap: 8px;
    background: var(--green); color: var(--white);
    font: 700 18px/1 "Open Sans", Arial, sans-serif; text-transform: uppercase;
    padding: 0 26px; height: 56px; border-radius: 2px;
  }
  .btn svg { width: 12px; height: 12px; }

  /* Hero */
  .hero { position: absolute; left: 0; top: 0; width: 1200px; height: 758px; overflow: hidden; }
  .hero-photo {
    position: absolute; inset: 0;
    background:
      linear-gradient(180deg, rgba(255,255,255,0.95) 0%, rgba(255,255,255,0) 22%),
      linear-gradient(100deg, #a8b4c2 0%, #8d9eb2 30%, #4c5f78 55%, #2f3f58 75%, #5a6e88 100%);
  }
  .logo { position: absolute; left: 80px; top: 34px; color: var(--blue); font-family: "Raleway", Arial, sans-serif; font-weight: 500; }
  .logo-name { font-size: 38px; line-height: 1.1; }
  .logo-sub { font-size: 22px; letter-spacing: 9px; }
  .main-nav { position: absolute; right: 80px; top: 58px; display: flex; gap: 40px; font: 400 21px "Raleway", Arial, sans-serif; color: #555; text-transform: uppercase; }
  .main-nav .active { color: var(--blue); }
  .hero-title { position: absolute; left: 80px; top: 246px; width: 560px; color: var(--blue); font: 700 40px/1.25 "Raleway", Arial, sans-serif; text-transform: uppercase; }
  .hero-call { position: absolute; left: 80px; top: 363px; display: flex; align-items: center; gap: 14px; color: var(--ink); font: 700 40px "Open Sans", Arial, sans-serif; text-transform: uppercase; }
  .hero-call svg { width: 56px; height: 56px; }
  .hero .btn { position: absolute; left: 78px; top: 431px; }

  /* Band */
  .band { position: absolute; left: 0; top: 758px; width: 1200px; height: 126px; background: var(--band); display: flex; align-items: center; justify-content: space-between; padding: 0 78px 0 80px; }
  .band-text { color: var(--white); font: 400 45px "Raleway", Arial, sans-serif; }

  /* Welcome */
  .welcome { position: absolute; left: 0; top: 884px; width: 1200px; height: 316px; text-align: center; }
  .welcome h1 { margin-top: 47px; font: 400 44px "Raleway", Arial, sans-serif; color: var(--green); text-transform: uppercase; }
  .welcome h1 span { color: var(--blue); }
  .welcome p { width: 940px; margin: 16px auto 0; font-size: 14.5px; line-height: 25px; }
  .welcome .btn { margin-top: 24px; }

  /* Services */
  .service { position: absolute; left: 0; width: 1200px; }
  .service.shaded { background: var(--grey-bg); }
  .service-copy { position: absolute; top: 56px; width: 560px; }
  .service h2 { font: 400 40px "Raleway", Arial, sans-serif; color: var(--green); }
  .service h2 span { color: var(--blue); }
  .service p { margin-top: 16px; font-size: 14.5px; line-height: 25px; }
  .service .btn { margin-top: 16px; }
  .service-image { position: absolute; border-radius: 4px; }

  .equipment { top: 1200px; height: 386px; }
  .business { top: 1586px; height: 387px; }
  .commercial { top: 1973px; height: 387px; }
  .construction { top: 2360px; height: 381px; }
  .bridging { top: 2741px; height: 384px; }
  .bridging-photo { position: absolute; inset: 0; background: linear-gradient(90deg, #f3f6f8 0%, #e6edf2 40%, #b9cbd8 68%, #7b98b0 100%); }

  /* News */
  .news { position: absolute; left: 0; top: 3125px; width: 1200px; height: 460px; }
  .news h2 { text-align: center; margin-top: 52px; font: 400 42px "Raleway", Arial, sans-serif; color: var(--green); text-transform: uppercase; }
  .news-list { position: absolute; left: 78px; top: 121px; display: flex; gap: 37px; }
  .news-card { width: 234px; }
  .news-thumb { width: 234px; height: 145px; }
  .news-card h3 { margin-top: 14px; font: 400 15px "Open Sans", Arial, sans-serif; color: var(--blue); }
  .news-date { display: flex; align-items: center; gap: 6px; margin-top: 4px; font-size: 13px; color: #888; }
  .news-date svg { width: 12px; height: 12px; }
  .news-card p { margin-top: 6px; font-size: 14.5px; line-height: 25px; }

  /* Footer */
  .site-footer { position: absolute; left: 0; top: 3585px; width: 1200px; height: 181px; background: var(--footer); color: var(--white); }
  .footer-nav { position: absolute; left: 80px; top: 28px; display: flex; gap: 30px; font-size: 17px; }
  .social { position: absolute; right: 80px; top: 16px; display: flex; gap: 12px; }
  .social-link { width: 48px; height: 48px; border-radius: 50%; border: 2px solid var(--footer-ring); display: flex; align-items: center; justify-content: center; }
  .social-link::after { content: ""; width: 12px; height: 12px; border-radius: 50%; background: var(--white); }
  .social-link.current { background: var(--green); border-color: var(--green); }
  .footer-rule { position: absolute; left: 0; top: 84px; width: 1200px; height: 1px; background: var(--footer-line); }
  .info-item { position: absolute; top: 104px; height: 46px; display: flex; align-items: center; gap: 14px; font-size: 15px; line-height: 22px; }
  .info-item svg { width: 46px; height: 46px; flex: none; }
  .info-address { left: 80px; width: 250px; }
  .info-phone { left: 350px; width: 230px; font-weight: 700; font-size: 19px; }
  .info-mail { left: 620px; width: 258px; font-size: 14px; white-space: nowrap; }
  .copyright { position: absolute; left: 892px; top: 106px; width: 230px; font-size: 14px; line-height: 21px; }
  .copyright b { color: var(--green); }
</style>
</head>
<body>

<header class="hero">
  <div class="hero-photo" role="img" aria-label="Photo of two businessmen in suits reviewing documents at a desk with a laptop"></div>
  <div class="logo">
    <div class="logo-name">Marcus Delbridge</div>
    <div class="logo-sub">Finance</div>
  </div>
  <nav class="main-nav">
    <span class="active">Home</span><span>About</span><span>Services</span><span>Contact</span>
  </nav>
  <h2 class="hero-title">Lorem Ipsum is simply dummy text.</h2>
  <div class="hero-call">
    Call us
    <svg viewBox="0 0 58 58" aria-hidden="true"><circle cx="29" cy="29" r="26" fill="none" stroke="#222" stroke-width="3"/><path d="M21 17c2-1 4 0 5 2l2 4c1 2 0 3-1 4l-1 1c1 3 4 6 7 7l1-1c1-1 2-2 4-1l4 2c2 1 3 3 2 5l-1 2c-1 2-4 3-7 2-9-3-15-9-18-18-1-3 0-6 2-7z" fill="#222"/></svg>
    123 456 7890
  </div>
  <span class="btn">Get a quote <svg viewBox="0 0 12 12"><path d="M2 6h7M6 2l4 4-4 4" stroke="#fff" stroke-width="2.4" fill="none"/></svg></span>
</header>

<section class="band">
  <p class="band-text">Lorem Ipsum is simply dummy text.</p>
  <span class="btn">Contact us <svg viewBox="0 0 12 12"><path d="M2 6h7M6 2l4 4-4 4" stroke="#fff" stroke-width="2.4" fill="none"/></svg></span>
</section>

<section class="welcome">
  <h1>Welcome to <span>Marcus Delbridge Finance</span></h1>
  <p>Lorem Ipsum is dummy text of the printing and typesetting industry. Lorem Ipsum has been the industry's standard dummy text ever since the 1500s, when an unknown printer took a galley of type it to make a type specimen book. It has survived not only five centuries, but also the leap into electronic typesetting, remaining essentially unchanged.</p>
  <span class="btn">Read more</span>
</section>

<section class="service equipment shaded">
  <div class="service-copy" style="left:80px;">
    <h2>Equipment <span>Finance</span></h2>
    <p>Lorem Ipsum is dummy text of the printing and typesetting industry. Lorem Ipsum has been the industry's standard dummy text ever since the 1500s, when an unknown printer took a galley of type it to make a type specimen book. It has survived not only five centuries, but also the leap into electronic typesetting, remaining essentially unchanged.</p>
    <span class="btn">Read more</span>
  </div>
  <div class="service-image" style="left:703px;top:43px;width:378px;height:277px;background:radial-gradient(ellipse at center,#cfd8e2 0%,#e8edf1 60%,var(--grey-bg) 100%);" role="img" aria-label="Illustration of a tablet with financial charts, a smartphone, a coffee cup and printed reports"></div>
</section>

<section class="service business">
  <div class="service-image" style="left:113px;top:0;width:402px;height:365px;background:radial-gradient(ellipse at 55% 60%,#6fb0d8 0%,#b8d8ea 45%,#fff 75%);" role="img" aria-label="Illustration of a hand placing a bar on a colourful 3D bar chart standing on a tablet"></div>
  <div class="service-copy" style="left:555px;">
    <h2>Business <span>Finance</span></h2>
    <p>Lorem Ipsum is dummy text of the printing and typesetting industry. Lorem Ipsum has been the industry's standard dummy text ever since the 1500s, when an unknown printer took a galley of type it to make a type specimen book. It has survived not only five centuries, but also the leap into electronic typesetting, remaining essentially unchanged.</p>
    <span class="btn">Read more</span>
  </div>
</section>

<section class="service commercial shaded">
  <div class="service-copy" style="left:80px;">
    <h2>Commercial <span>Finance</span></h2>
    <p>Lorem Ipsum is dummy text of the printing and typesetting industry. Lorem Ipsum has been the industry's standard dummy text ever since the 1500s, when an unknown printer took a galley of type it to make a type specimen book. It has survived not only five centuries, but also the leap into electronic typesetting, remaining essentially unchanged.</p>
    <span class="btn">Read more</span>
  </div>
  <div class="service-image" style="left:693px;top:12px;width:392px;height:362px;background:radial-gradient(circle at center,#e9ecef 0%,#9aa6b3 45%,#5d6d7e 58%,var(--grey-bg) 72%);border-radius:50%;" role="img" aria-label="Overhead photo of business people seated around a meeting table"></div>
</section>

<section class="service construction">
  <div class="service-image" style="left:113px;top:40px;width:402px;height:300px;background:linear-gradient(135deg,#fff 0%,#d9dde2 40%,#b4bcc5 60%,#fff 100%);" role="img" aria-label="Illustration of a 3D house model with red walls over architectural blueprints"></div>
  <div class="service-copy" style="left:555px;">
    <h2>Construction <span>Finance</span></h2>
    <p>Lorem Ipsum is dummy text of the printing and typesetting industry. Lorem Ipsum has been the industry's standard dummy text ever since the 1500s, when an unknown printer took a galley of type it to make a type specimen book. It has survived not only five centuries, but also the leap into electronic typesetting, remaining essentially unchanged.</p>
    <span class="btn">Read more</span>
  </div>
</section>

<section class="service bridging">
  <div class="bridging-photo" role="img" aria-label="Photo of a suspension bridge rising from fog under a pale blue sky"></div>
  <div class="service-copy" style="left:80px;">
    <h2>Bridging <span>Finance</span></h2>
    <p>Lorem Ipsum is dummy text of the printing and typesetting industry. Lorem Ipsum has been the industry's standard dummy text ever since the 1500s, when an unknown printer took a galley of type it to make a type specimen book. It has survived not only five centuries, but also the leap into electronic typesetting, remaining essentially unchanged.</p>
    <span class="btn">Read more</span>
  </div>
</section>

<section class="news">
  <h2>Latest news</h2>
  <div class="news-list">
    <article class="news-card">
      <div class="news-thumb" role="img" aria-label="Photo of two people shaking hands" style="background:linear-gradient(135deg,#2d3b4f,#7b8ea5 60%,#c9d3dd);"></div>
      <h3>Lorem Ipsum is dummy text.</h3>
      <div class="news-date"><svg viewBox="0 0 12 12"><rect x="1" y="2" width="10" height="9" fill="none" stroke="#888"/><path d="M1 5h10" stroke="#888"/></svg>09 January 2017</div>
      <p>Lorem Ipsum is dummy text of the printing and typesetting industry standard.</p>
    </article>
    <article class="news-card">
      <div class="news-thumb" role="img" aria-label="Photo of a hand pointing at charts on a tablet" style="background:linear-gradient(135deg,#e4eef4,#9cc4dc 55%,#5a8fb2);"></div>
      <h3>Lorem Ipsum is dummy text.</h3>
      <div class="news-date"><svg viewBox="0 0 12 12"><rect x="1" y="2" width="10" height="9" fill="none" stroke="#888"/><path d="M1 5h10" stroke="#888"/></svg>09 January 2017</div>
      <p>Lorem Ipsum is dummy text of the printing and typesetting industry standard.</p>
    </article>
    <article class="news-card">
      <div class="news-thumb" role="img" aria-label="Photo of a long bridge at sunset over water" style="background:linear-gradient(180deg,#6f8fb0,#d9b48a 55%,#4a5a6a);"></div>
      <h3>Lorem Ipsum is dummy text.</h3>
      <div class="news-date"><svg viewBox="0 0 12 12"><rect x="1" y="2" width="10" height="9" fill="none" stroke="#888"/><path d="M1 5h10" stroke="#888"/></svg>09 January 2017</div>
      <p>Lorem Ipsum is dummy text of the printing and typesetting industry standard.</p>
    </article>
    <article class="news-card">
      <div class="news-thumb" role="img" aria-label="Photo of colleagues meeting around an office table" style="background:linear-gradient(135deg,#f0f2f4,#b9c3cc 50%,#6e7f90);"></div>
      <h3>Lorem Ipsum is dummy text.</h3>
      <div class="news-date"><svg viewBox="0 0 12 12"><rect x="1" y="2" width="10" height="9" fill="none" stroke="#888"/><path d="M1 5h10" stroke="#888"/></svg>09 January 2017</div>
      <p>Lorem Ipsum is dummy text of the printing and typesetting industry standard.</p>
    </article>
  </div>
</section>

<footer class="site-footer">
  <nav class="footer-nav"><span>Home</span><span>About</span><span>Services</span><span>Contact</span></nav>
  <div class="social" aria-label="Social links">
    <span class="social-link current"></span><span class="social-link"></span><span class="social-link"></span>
  </div>
  <div class="footer-rule"></div>
  <div class="info-item info-address">
    <svg viewBox="0 0 46 46" aria-hidden="true"><circle cx="23" cy="23" r="21" fill="none" stroke="#a2bd1e" stroke-width="2"/><path d="M23 13c-4 0-7 3-7 7 0 5 7 13 7 13s7-8 7-13c0-4-3-7-7-7z" fill="none" stroke="#a2bd1e" stroke-width="2"/><circle cx="23" cy="20" r="2.5" fill="#a2bd1e"/></svg>
    <span>Lorem Ipsum is dummy text of the printing.</span>
  </div>
  <div class="info-item info-phone">
    <svg viewBox="0 0 46 46" aria-hidden="true"><circle cx="23" cy="23" r="21" fill="none" stroke="#a2bd1e" stroke-width="2"/><path d="M17 14c1.5-.7 3 0 3.7 1.5l1.4 3c.6 1.4 0 2.3-.8 3l-.6.6c.8 2.2 3 4.4 5.2 5.2l.6-.6c.7-.8 1.6-1.4 3-.8l3 1.4c1.5.7 2.2 2.2 1.5 3.7l-.7 1.4c-.8 1.5-3 2.2-5 1.5-6.6-2.2-11-6.6-13.2-13.2-.7-2 0-4.2 1.5-5z" fill="#a2bd1e"/></svg>
    <span>123 456 7890</span>
  </div>
  <div class="info-item info-mail">
    <svg viewBox="0 0 46 46" aria-hidden="true"><circle cx="23" cy="23" r="21" fill="none" stroke="#a2bd1e" stroke-width="2"/><rect x="13" y="16" width="20" height="14" fill="none" stroke="#a2bd1e" stroke-width="2"/><path d="M13 16l10 8 10-8" fill="none" stroke="#a2bd1e" stroke-width="2"/></svg>
    <span>info@marcusdelbridge.com</span>
  </div>
  <p class="copyright">© <b>Marcus Delbridge</b> - 2017. All Rights Reserved.</p>
</footer>

</body>
</html>
```